Plantain chip snack pack bag design + company logo design

We need to design a bag for a new snack food company. The brand is called "Crisp Joyla," and the first product, plantain chips, will come in 4 flavors - Classic Unripe, Sweet 'n Spicy!!, Original Sweet, and Ginger & Soy. The bag - which we plan to print in multiple sizes - needs to have a clear section on the front so the contents are visible, as they will be sold by street vendors and ability to view the contents is key. Design needs to be "very happy and exciting" and feature simple, strong colors that say "delicious and crispy" i.e. Classic Unripe is green, Sweet 'n Spicy!! is red, Original Sweet is yellow, and Ginger & Soy is tan (plus these will be printed in mass so must be simple yet very catchy on shelves and on the street vendors). On the back, there needs to be a column of nutritional content, plus the company contact address, email, phone lines, Twitter/Facebook/Instagram handles, and the quality certification number. Also, on the back, a bar code and "Made in xxx" text. Finally, the net weight of contents needs to be on the front as well. I have uploaded a sample of a competing product's packaging as inspiration only (NOT TO BE COPIED but to our design MUST BE MORE CATCHY, ATTRACTIVE, and FUN than this one)

Target Market(s)

All snack consumers, especially those with a bias toward healthier eating.

Industry/Entity Type

It Company

Logo Text

Delight in every bite!

Font styles to use
Serif
Decorative
Script

Requirements
Must have
• 1. For the package design, handoffs must include placeholders for ALL text so we can edit the text as needed
• 2. For package design, large transparent section on bag is critical so contents are visible; also, branding of "Crisp Joyla" must be large and recognizable from a distance
• 3. Primary colors suitable for industrial mass production
• 4. Logo design on the bags must include the parent company name i.e. "Crisp Joyla Snacks by Volunta Foods"
• 5. Package must say "Plantain chips" and the flavor e.g. "Sweet 'n Spicy!!" and with a small image of a hot pepper (each flavor should have a similar small image representing the flavor)
• 6. For the Logo design portion of the project, the Volunta Foods Limited logo should incorporate plantains, coconuts, potatos and corn. This logo is for the parent company and Crisp Joyla is the plantain chip product line
Nice to have
• 1. Smiling faces suggesting happiness, health, friendliness, and overall delight at eating the chips

```html
<!DOCTYPE html>
<html lang="en">
<head>
<meta charset="utf-8">
<title>Crisp Joyla Plantain Chips – Pack Fronts</title>
<link rel="stylesheet" href="https://fonts.googleapis.com/css2?family=Fredoka:wght@600;700&display=swap">
<style>
  :root{
    --backdrop:#c9c9c9;
    --bag-black:#0b0b0b;
    --window:#ffffff;
    --window-edge:#f4ea12;
    --outline:#3b2a0e;
    --brand:#d9261f;
    --sun:#f6b53a;
    --green:#3fc41a;
    --red:#d61f1b;
    --orange:#f29a12;
    --yellow:#f1e41c;
  }
  html,body{margin:0;padding:0;overflow:hidden}
  body{width:1200px;height:776px;background:var(--backdrop);position:relative;font-family:"Fredoka",sans-serif}
  .pack{position:absolute;display:block}
  .pack--large{top:62px;width:232px;height:309px}
  .pack--small{top:443px;width:172px;height:229px}
  .flavor-classic{--flavor:var(--green)}
  .flavor-spicy{--flavor:var(--red)}
  .flavor-ginger{--flavor:var(--orange)}
  .flavor-sweet{--flavor:var(--yellow)}
  .brand-name{font-family:"Fredoka",sans-serif;font-weight:700;font-size:17px;fill:var(--brand)}
  .product-title{font-family:"Fredoka",sans-serif;font-weight:700;font-size:27px;fill:var(--flavor);stroke:var(--outline);stroke-width:3.4px;paint-order:stroke;stroke-linejoin:round}
  .badge-text{font-family:"Fredoka",sans-serif;font-weight:700;font-size:5px;fill:var(--outline);letter-spacing:.3px}
  .defs{position:absolute;width:0;height:0}
</style>
</head>
<body>

<svg class="defs" aria-hidden="true">
  <defs>
    <radialGradient id="ray-glow" cx="0.45" cy="0.4" r="0.85">
      <stop offset="0" stop-color="#262626"/>
      <stop offset="1" stop-color="#0b0b0b"/>
    </radialGradient>
    <path id="badge-arc-top" d="M138,160 A12,12 0 0 1 162,160"/>
    <path id="badge-arc-bottom" d="M134,160 A16,16 0 0 0 166,160"/>
    <symbol id="label-base" viewBox="0 0 172 229">
      <rect class="bag-body" width="172" height="229" fill="url(#ray-glow)"/>
      <!-- clear viewing window -->
      <path class="window-edge" d="M0,150 C50,140 110,128 172,124 L172,186 C120,189 50,196 0,207 Z" fill="var(--window-edge)"/>
      <path class="window" d="M0,150 C50,140 110,128 172,124 L172,180 C120,183 50,190 0,201 Z" fill="var(--window)"/>
      <!-- brand mark -->
      <circle cx="104" cy="28" r="18" fill="var(--sun)"/>
      <text class="brand-name" x="86" y="66" text-anchor="middle">Crisp Joyla</text>
      <!-- product title -->
      <text class="product-title" x="86" y="98" text-anchor="middle">Plantain</text>
      <text class="product-title" x="84" y="123" text-anchor="middle">Chips</text>
      <!-- flavor badge -->
      <circle cx="150" cy="160" r="19" fill="var(--flavor)" stroke="var(--outline)" stroke-width="1.6"/>
      <circle cx="150" cy="160" r="6" fill="var(--outline)" opacity=".55" role="img" aria-label="Small flavor illustration"/>
    </symbol>
  </defs>
</svg>

<!-- large packs -->
<svg class="pack pack--large flavor-classic" style="left:80px" viewBox="0 0 172 229" role="img" aria-label="Crisp Joyla Plantain Chips, Classic Unripe">
  <use href="#label-base"/>
  <text class="badge-text"><textPath href="#badge-arc-top" startOffset="50%" text-anchor="middle">CLASSIC</textPath></text>
  <text class="badge-text"><textPath href="#badge-arc-bottom" startOffset="50%" text-anchor="middle">UNRIPE</textPath></text>
</svg>
<svg class="pack pack--large flavor-spicy" style="left:350px" viewBox="0 0 172 229" role="img" aria-label="Crisp Joyla Plantain Chips, Sweet n' Spicy">
  <use href="#label-base"/>
  <text class="badge-text"><textPath href="#badge-arc-top" startOffset="50%" text-anchor="middle">SWEET</textPath></text>
  <text class="badge-text"><textPath href="#badge-arc-bottom" startOffset="50%" text-anchor="middle">N' SPICY</textPath></text>
</svg>
<svg class="pack pack--large flavor-ginger" style="left:620px" viewBox="0 0 172 229" role="img" aria-label="Crisp Joyla Plantain Chips, Ginger and Soy">
  <use href="#label-base"/>
  <text class="badge-text"><textPath href="#badge-arc-top" startOffset="50%" text-anchor="middle">GINGER</textPath></text>
  <text class="badge-text"><textPath href="#badge-arc-bottom" startOffset="50%" text-anchor="middle">AND SOY</textPath></text>
</svg>
<svg class="pack pack--large flavor-sweet" style="left:890px" viewBox="0 0 172 229" role="img" aria-label="Crisp Joyla Plantain Chips, Original Sweet">
  <use href="#label-base"/>
  <text class="badge-text"><textPath href="#badge-arc-top" startOffset="50%" text-anchor="middle">ORIGINAL</textPath></text>
  <text class="badge-text"><textPath href="#badge-arc-bottom" startOffset="50%" text-anchor="middle">SWEET</textPath></text>
</svg>

<!-- small flat labels -->
<svg class="pack pack--small flavor-classic" style="left:121px" viewBox="0 0 172 229" role="img" aria-label="Crisp Joyla Plantain Chips label, Classic Unripe">
  <use href="#label-base"/>
  <text class="badge-text"><textPath href="#badge-arc-top" startOffset="50%" text-anchor="middle">CLASSIC</textPath></text>
  <text class="badge-text"><textPath href="#badge-arc-bottom" startOffset="50%" text-anchor="middle">UNRIPE</textPath></text>
</svg>
<svg class="pack pack--small flavor-spicy" style="left:388px" viewBox="0 0 172 229" role="img" aria-label="Crisp Joyla Plantain Chips label, Sweet n' Spicy">
  <use href="#label-base"/>
  <text class="badge-text"><textPath href="#badge-arc-top" startOffset="50%" text-anchor="middle">SWEET</textPath></text>
  <text class="badge-text"><textPath href="#badge-arc-bottom" startOffset="50%" text-anchor="middle">N' SPICY</textPath></text>
</svg>
<svg class="pack pack--small flavor-ginger" style="left:657px" viewBox="0 0 172 229" role="img" aria-label="Crisp Joyla Plantain Chips label, Ginger and Soy">
  <use href="#label-base"/>
  <text class="badge-text"><textPath href="#badge-arc-top" startOffset="50%" text-anchor="middle">GINGER</textPath></text>
  <text class="badge-text"><textPath href="#badge-arc-bottom" startOffset="50%" text-anchor="middle">AND SOY</textPath></text>
</svg>
<svg class="pack pack--small flavor-sweet" style="left:924px" viewBox="0 0 172 229" role="img" aria-label="Crisp Joyla Plantain Chips label, Original Sweet">
  <use href="#label-base"/>
  <text class="badge-text"><textPath href="#badge-arc-top" startOffset="50%" text-anchor="middle">ORIGINAL</textPath></text>
  <text class="badge-text"><textPath href="#badge-arc-bottom" startOffset="50%" text-anchor="middle">SWEET</textPath></text>
</svg>

</body>
</html>
```